Tallwick Home Services Web Site

Design Web site with 3-4 pages: Home, About Us, Services and Order form / Schedule Appointment (which will likely be link to Method App and Quickbooks integration.)
Services include: Dryer Vent Cleaning, AC Cleaning, Difficult-to-Reach Light Bulb replacement, Wood Repair and Home Maintenance Plans including Fire Safety Checks and Filter Replacement.

Target Market(s)

Luxury Home Owners, Professionals (Dr's/lawyers) and Seniors

Industry/Entity Type

Home Maintenance

Coding

Coded - Design and coding required

Requirements
Must have
• Tagline - Where Home Maintenance is Elementary

```html
<!DOCTYPE html>
<html lang="en">
<head>
<meta charset="utf-8">
<title>Tallwick Home Services</title>
<link rel="stylesheet" href="https://fonts.googleapis.com/css2?family=Poppins:wght@300;400;500;600;700;800&display=swap">
<style>
:root{
  --gold:#e3a92b;
  --gold-soft:#f0c85a;
  --slate:#6d6e73;
  --slate-dark:#55565b;
  --ink:#3a3b3f;
  --text:#5c5d62;
  --light:#f4f4f4;
  --white:#ffffff;
}
*{margin:0;padding:0;box-sizing:border-box}
html,body{width:1200px;height:3741px;overflow:hidden}
body{position:relative;font-family:"Poppins",sans-serif;color:var(--text);background:var(--white)}
.abs{position:absolute}
.btn{position:absolute;display:flex;align-items:center;justify-content:center;border-radius:30px;background:var(--gold);color:var(--white);font-weight:700;font-size:11.5px;letter-spacing:.2px;text-transform:uppercase}
.btn.slate{background:var(--slate)}
.eyebrow{position:absolute;display:flex;align-items:center;gap:10px;font-size:11.5px;color:var(--gold);text-transform:uppercase}
.eyebrow i{display:block;width:78px;height:1.5px;background:var(--gold)}
.title{position:absolute;font-weight:700;font-size:31px;line-height:1.15;color:var(--ink);text-transform:uppercase}
.title em{font-style:normal;color:var(--gold)}
.photo{position:absolute}

/* header */
.topbar{left:443px;top:0;width:757px;height:44px;background:var(--slate);clip-path:polygon(0 0,100% 0,100% 100%,40px 100%)}
.top-icon{position:absolute;top:6px;width:32px;height:32px;border-radius:50%;background:#86878c}
.top-text{position:absolute;color:var(--white);font-size:11px;top:14px}
.search{left:936px;top:6px;width:187px;height:32px;border-radius:16px;background:var(--white)}
.search span{position:absolute;left:14px;top:8px;font-size:10px;color:#b7b7b7}
.search b{position:absolute;right:4px;top:4px;width:24px;height:24px;border-radius:50%;background:var(--gold)}
.brand{position:absolute;display:flex;flex-direction:column;align-items:center}
.brand .dot{width:38px;height:38px;border-radius:50%;background:var(--gold)}
.brand .name{font-weight:700;color:var(--gold);letter-spacing:2px;margin-top:6px}
.brand .sub{font-size:11px;color:var(--slate);letter-spacing:1px}
.nav{position:absolute;top:77px;font-size:12px;font-weight:600;color:var(--ink)}

/* hero */
.hero{left:0;top:126px;width:1200px;height:506px;background:linear-gradient(90deg,#5e5f63 0%,#7b7c80 45%,#9a9ca1 70%,#6d7380 100%)}
.hero-copy{color:var(--white)}
.hero h1{position:absolute;left:75px;top:288px;font-size:49px;line-height:54px;font-weight:800;color:var(--white)}
.hero h1 em{font-style:normal;color:var(--gold)}

/* why */
.why{left:0;top:632px;width:1200px;height:388px;background:var(--light)}
.why-item{position:absolute;width:200px;text-align:center;font-size:11px;font-weight:600;line-height:17px;color:var(--ink)}
.why-item .icon{width:78px;height:78px;border-radius:50%;background:var(--slate);margin:0 auto 26px}
.why-item.on{color:var(--gold)}
.why-item.on .icon{background:var(--gold)}

/* about */
.about p{position:absolute;left:624px;width:430px;font-size:11.5px;line-height:19px;color:var(--text)}
.value{position:absolute;font-size:11.5px;display:flex;align-items:center;gap:6px}
.value i{display:block;width:12px;height:12px;border-radius:50%;background:var(--gold)}

/* services */
.svc{position:absolute;width:170px;text-align:center;color:var(--white)}
.svc .icon{width:62px;height:62px;border-radius:50%;background:var(--white);margin:0 auto 12px;display:flex;align-items:center;justify-content:center}
.svc .icon i{display:block;width:28px;height:28px;border-radius:6px;background:var(--gold)}
.svc h3{font-size:11px;font-weight:700;line-height:15px;text-transform:uppercase}
.svc p{font-size:12px;line-height:19px;margin-top:5px;padding:0 14px}
.svc-div{position:absolute;top:1945px;width:1px;height:160px;background:rgba(255,255,255,.25)}

/* testimonial */
.quote{position:absolute;left:75px;top:2512px;width:520px;font-size:21.5px;line-height:30px;font-weight:400;color:var(--text)}
.dash{position:absolute;top:2630px;width:44px;height:3px;border-radius:2px;background:#c9c9c9}

/* booking */
.book{left:0;top:2834px;width:1200px;height:508px;background:var(--gold)}

/* footer */
.fcol h4{position:absolute;font-size:13px;font-weight:600;color:var(--ink);border-left:2px solid var(--gold);padding-left:8px;line-height:14px}
.flink{position:absolute;font-size:10px;color:#9a9a9a}
.social{position:absolute;top:3547px;width:22px;height:22px;border-radius:50%;background:var(--gold)}
</style>
</head>
<body>

<!-- header -->
<div class="abs topbar"></div>
<div class="top-icon" style="left:490px"></div>
<div class="top-text" style="left:532px">info@tallwickhome.example</div>
<div class="top-icon" style="left:752px"></div>
<div class="top-text" style="left:795px;font-weight:700;font-size:13px;top:12px">(+321)555-0142</div>
<div class="abs search"><span>Home Services</span><b></b></div>

<div class="brand" style="left:75px;top:14px;width:150px">
  <div class="dot"></div>
  <div class="name" style="font-size:24px">TALLWICK</div>
  <div class="sub">HOME SERVICES</div>
</div>
<div class="nav" style="left:622px;color:var(--gold)">⌂ HOME</div>
<div class="nav" style="left:715px">ABOUT US</div>
<div class="nav" style="left:814px">SERVICES</div>
<div class="btn" style="left:907px;top:61px;width:218px;height:45px">Schedule Appointment</div>

<!-- hero -->
<div class="abs hero" role="img" aria-label="Technician in a plaid shirt fixing a ceiling light fixture"></div>
<div class="abs hero-copy" style="left:75px;top:266px;font-size:11px;display:flex;align-items:center;gap:14px">WELCOME TO TALLWICK HOME SERVICES <i style="display:block;width:78px;height:1.5px;background:#fff"></i></div>
<div class="hero"><h1>WHERE HOME<br><em>MAINTENANCE</em> IS<br>ELEMENTARY</h1></div>
<div class="abs hero-copy" style="left:75px;top:460px;width:430px;font-size:11.5px;line-height:19px">From dryer vent cleaning to home safety checks, we make sure your home runs smoothly, safely, and worry-free</div>
<div class="btn" style="left:75px;top:516px;width:285px;height:43px">Schedule Your Appointment Today</div>

<!-- why choose -->
<div class="abs why"></div>
<div class="eyebrow" style="left:440px;top:721px"><i></i>Why Choose Us Section<i></i></div>
<div class="title" style="left:0;width:1200px;text-align:center;top:743px">Why <em>Choose</em> Us Section</div>
<div class="why-item" style="left:162px;top:837px"><div class="icon"></div>TRUSTED BY LUXURY<br>HOME OWNERS</div>
<div class="why-item" style="left:358px;top:837px"><div class="icon"></div>TAILORED SERVICES<br>FOR SENIORS</div>
<div class="why-item on" style="left:558px;top:837px"><div class="icon"></div>LICENSED, INSURED,<br>AND DETAIL-ORIENTED</div>
<div class="why-item" style="left:774px;top:837px;width:240px"><div class="icon"></div>PROFESSIONALS' FIRST CHOICE<br>(DOCTORS, LAWYERS, EXECUTIVES)</div>

<!-- about -->
<div class="photo" style="left:151px;top:1133px;width:177px;height:247px;border-radius:0 177px 0 0;background:linear-gradient(135deg,#ddd,#f2f2f2)" role="img" aria-label="Hands measuring a plan with a level and pencil"></div>
<div class="photo" style="left:365px;top:1133px;width:177px;height:247px;border-radius:177px 0 0 0;background:linear-gradient(135deg,#8a7a66,#c9b79c)" role="img" aria-label="Carpenter with ear protection working on wood"></div>
<div class="photo" style="left:151px;top:1417px;width:177px;height:181px;background:linear-gradient(135deg,#c8c8c8,#8f8f8f)" role="img" aria-label="Worker servicing a dryer in a laundry room"></div>
<div class="photo" style="left:365px;top:1417px;width:177px;height:178px;background:linear-gradient(135deg,#b9c2cc,#d7b24a)" role="img" aria-label="Technician in a hard hat checking an appliance"></div>

<div class="eyebrow" style="left:624px;top:1177px"><i></i>About Us<i></i></div>
<div class="title" style="left:624px;top:1199px;line-height:35px">Committed to Simplifying<br>Home <em>Maintenance</em></div>
<div class="about">
<p style="top:1280px">We understand that maintaining a home can be time-consuming and complex—especially for busy professionals and seniors who value their time. Our mission is simple: to take the hassle out of every-day upkeep while keeping your home safe, efficient, and beautiful.</p>
<p style="top:1374px">Our team combines experience, professionalism, and care to deliver services tailored to luxury homeowners, doctors, lawyers, and retirees who deserve stress-free maintenance.</p>
</div>
<div class="abs" style="left:627px;top:1444px;font-size:12px;font-weight:700;color:var(--gold)">CORE VALUES</div>
<div class="value" style="left:627px;top:1471px"><i></i>Integrity and Trust</div>
<div class="value" style="left:779px;top:1471px"><i></i>Attention to Detail</div>
<div class="value" style="left:627px;top:1500px"><i></i>Safety First</div>
<div class="value" style="left:779px;top:1500px"><i></i>Long-Term Reliability</div>
<div class="btn" style="left:623px;top:1546px;width:287px;height:46px">Learn More About Our Services</div>

<!-- quick services -->
<div class="abs" style="left:0;top:1751px;width:1200px;height:516px;background:linear-gradient(180deg,#6b6c71,#76777c)" role="img" aria-label="Faded photo of a home interior behind the services"></div>
<svg class="abs" style="left:0;top:1700px" width="1200" height="567" viewBox="0 0 1200 567">
  <path d="M0,0 H1200 V225 Q600,-211 0,225 Z" fill="#fff"/>
  <path d="M0,225 Q600,-211 1200,225 Q600,-123 0,225 Z" fill="#e3a92b"/>
</svg>
<div class="eyebrow" style="left:466px;top:1843px"><i></i>Quick Services<i></i></div>
<div class="title" style="left:0;width:1200px;text-align:center;top:1864px;color:#fff">Quick <em>Services</em></div>
<div class="svc" style="left:129px;top:1941px"><div class="icon"><i></i></div><h3>Dryer Vent Cleaning</h3><p>Prevent fire hazards and improve efficiency with a thorough cleaning of your dryer vents.</p></div>
<div class="svc-div" style="left:326px"></div>
<div class="svc" style="left:333px;top:1941px"><div class="icon"><i></i></div><h3>AC Cleaning</h3><p>Breathe fresh air and keep your cooling system running at peak performance.</p></div>
<div class="svc-div" style="left:506px"></div>
<div class="svc" style="left:515px;top:1941px"><div class="icon"><i></i></div><h3>Wood Repair</h3><p>No more struggling with ladders—let us handle those high or tricky spots safely.</p></div>
<div class="svc-div" style="left:686px"></div>
<div class="svc" style="left:707px;top:1941px"><div class="icon"><i></i></div><h3>Home Maintenance<br>Plans</h3><p>Comprehensive plans include:</p></div>
<div class="svc-div" style="left:880px"></div>
<div class="svc" style="left:900px;top:1941px"><div class="icon"><i></i></div><h3>Light Bulb Replacement (Hard-to-Reach Areas)</h3><p>No more struggling with ladders—let us handle those high or tricky spots safely.</p></div>
<div class="btn" style="left:456px;top:2137px;width:287px;height:47px">Schedule Your Service Today</div>

<!-- testimonial -->
<div class="abs" style="left:640px;top:2368px;width:515px;height:364px;border-radius:260px 260px 20px 20px;background:linear-gradient(180deg,#f6efe0,#f3dea8)" role="img" aria-label="Illustration of a house with ribbon and circular portraits of happy clients"></div>
<div class="eyebrow" style="left:75px;top:2450px"><i style="width:78px"></i>Testimonial<i></i></div>
<div class="title" style="left:75px;top:2472px;color:var(--slate)"><em>Testimonial</em> Preview</div>
<div class="quote">Finally a maintenance company that actually cares about details. Scheduling was simple and the service was excellent.</div>
<div class="abs" style="left:75px;top:2624px;font-size:11px;font-weight:700;color:var(--gold)">LOCAL HOMEOWNER</div>
<div class="dash" style="left:241px"></div>
<div class="dash" style="left:293px;background:var(--gold)"></div>
<div class="dash" style="left:345px"></div>
<div class="dash" style="left:396px"></div>

<!-- booking -->
<div class="abs book"></div>
<div class="abs" style="left:0;top:2834px;width:712px;height:508px;background:linear-gradient(135deg,#6a6b70,#8a8b90);clip-path:polygon(0 0,470px 0,712px 100%,0 100%)" role="img" aria-label="Hand holding a phone showing the appointment booking app"></div>
<div class="eyebrow" style="left:751px;top:3005px;color:#fff"><i style="background:#fff"></i>Schedule Appointment<i style="background:#fff"></i></div>
<div class="title" style="left:751px;top:3028px;color:#fff;line-height:35px">Book Your <span style="color:var(--slate)">Service</span><br><span style="color:var(--slate)">In</span> Minutes</div>
<div class="abs" style="left:751px;top:3108px;width:370px;font-size:11.5px;line-height:19px;color:#fff">Ready to simplify your home maintenance? Use our easy online scheduling form below. Choose your service, select your preferred date, and relax—our team will handle the rest.</div>
<div class="btn slate" style="left:750px;top:3185px;width:239px;height:45px">Schedule My Appointment</div>

<!-- footer -->
<div class="brand" style="left:138px;top:3444px;width:150px">
  <div class="dot" style="width:32px;height:32px"></div>
  <div class="name" style="font-size:20px">TALLWICK</div>
  <div class="sub" style="font-size:10px">HOME SERVICES</div>
</div>
<div class="social" style="left:156px"></div>
<div class="social" style="left:187px"></div>
<div class="social" style="left:218px"></div>
<div class="social" style="left:249px"></div>

<div class="fcol"><h4 style="left:382px;top:3448px">QUICK LINKS</h4></div>
<div class="flink" style="left:397px;top:3480px">Home</div>
<div class="flink" style="left:397px;top:3502px">About Us</div>
<div class="flink" style="left:397px;top:3525px">Services</div>
<div class="flink" style="left:397px;top:3547px">Schedule</div>
<div class="flink" style="left:397px;top:3570px">Appointment</div>

<div class="fcol"><h4 style="left:581px;top:3448px">CONTACT</h4></div>
<div class="flink" style="left:591px;top:3480px">Lindenweg 12 10115 Berlin</div>
<div class="flink" style="left:591px;top:3502px">(+321)555-0142</div>
<div class="flink" style="left:591px;top:3525px">info@tallwickhome.example</div>
<svg class="abs" style="left:574px;top:3480px" width="10" height="60" viewBox="0 0 10 60">
  <path d="M5 1a3.5 3.5 0 0 0-3.5 3.5C1.5 7 5 11 5 11s3.5-4 3.5-6.5A3.5 3.5 0 0 0 5 1z" fill="#e3a92b"/>
  <path d="M2 24c0 4 4 8 8 8l0-2-2-1-1 1c-2-1-3-2-4-4l1-1-1-2z" fill="#e3a92b"/>
  <rect x="1" y="47" width="8" height="6" fill="#e3a92b"/>
</svg>

<div class="fcol"><h4 style="left:812px;top:3448px">SERVICES</h4></div>
<div class="flink" style="left:822px;top:3480px">Dryer Vent Cleaning</div>
<div class="flink" style="left:822px;top:3502px">AC Cleaning</div>
<div class="flink" style="left:822px;top:3525px">Wood Repair</div>
<div class="flink" style="left:822px;top:3547px">Home Maintenance Plans</div>
<div class="flink" style="left:822px;top:3570px">Light Bulb Replacement (Hard-to-Reach Areas)</div>

<div class="abs" style="left:124px;top:3679px;width:952px;height:1px;background:#e6e6e6"></div>
<div class="flink" style="left:124px;top:3700px;font-size:9px">copyright © 2025 Tallwick Home Services</div>
<div class="flink" style="left:921px;top:3700px;font-size:9px">Privacy Policy | Terms &amp; Conditions</div>
<div class="abs" style="left:1151px;top:3660px;width:32px;height:32px;border-radius:50%;background:var(--gold)"></div>

</body>
</html>
```